Roofing Company Modern look

I want a modern and sophisticated look for our roofing business.

Our address is :

5217 Mallow Creek Ln
Orlando, Fl 32825

(407)-583-2196

www.HarborlineRoofsFl.com

I also want to make sure on the back there is a spot to put
Project Manager Name :

Number:

Because the cards will be used by all sales people

Project Manager Name :

Also there are accreditation we have logos are uploaded here as well that I would like maybe on the back of card as well

I also want to highlight our special attributions or trades:

Residential & Commercial
Fully Insured
License # CCC7482913
Insurance Claims
Serving Central Florida Since 1992
Free Estimates

Contact Information for Business Card

Our address is :

5217 Mallow Creek Ln
Orlando, Fl 32825

(407)-583-2196

Project Manager Name :

Residential & Commercial
Fully Insured
License # CCC7482913
Insurance Claims
Free Estimates

Font styles to use
Serif
Sans Serif

Colors
3176b5

Requirements
Must have
• Must have royal blue like my logo grey and black are the colors I like

```html
<!DOCTYPE html>
<html lang="en">
<head>
<meta charset="utf-8">
<title>Harborline Roofing &amp; Gutters – Business Card</title>
<link href="https://fonts.googleapis.com/css2?family=Questrial&family=Roboto+Condensed:wght@300;400&display=swap" rel="stylesheet">
<style>
  :root {
    --royal-blue: #3176b5;
    --deep-blue: #15609f;
    --sky-blue: #4fb3e3;
    --ink: #2c2c2c;
    --steel-grey: #5a5d62;
    --card-white: #ffffff;
    --backdrop: #e6e6e6;
    --badge-grey: #8d949c;
    --badge-red: #d7262e;
    --line-blue: #2a6aa3;
  }
  * { box-sizing: border-box; margin: 0; padding: 0; }
  html, body { width: 1200px; height: 1200px; overflow: hidden; }
  body { background: var(--backdrop); position: relative; font-family: "Questrial", sans-serif; }

  .card {
    position: absolute; left: 255px; width: 690px; height: 394px;
    border-radius: 20px; overflow: hidden; background: var(--card-white);
    box-shadow: 0 10px 24px rgba(0,0,0,0.18);
  }
  .card--front { top: 165px; }
  .card--back { top: 650px; }
  .card__art { position: absolute; inset: 0; width: 100%; height: 100%; }

  .brand { position: absolute; left: 52px; top: 118px; display: flex; align-items: center; gap: 14px; color: var(--royal-blue); }
  .brand__dot { width: 40px; height: 40px; border-radius: 50%; background: var(--royal-blue); flex: none; }
  .brand__name { font-size: 36px; line-height: 1; letter-spacing: 2px; font-weight: 400; }
  .brand__sub { font-size: 12.5px; letter-spacing: 2.4px; margin-top: 6px; font-weight: 400; }

  .badges { position: absolute; right: 48px; top: 45px; width: 140px; }
  .badges__row { display: flex; justify-content: space-between; align-items: center; }
  .badge-tall { width: 34px; height: 46px; background: #eef2f6; border: 2px solid var(--royal-blue); border-radius: 4px; }
  .badge-hex { width: 48px; height: 46px; background: var(--steel-grey); clip-path: polygon(50% 0, 100% 22%, 100% 78%, 50% 100%, 0 78%, 0 22%); }
  .badge-round { width: 44px; height: 44px; border-radius: 50%; background: #f3f3f3; border: 3px solid var(--badge-grey); }
  .badge-wide { margin-top: 9px; height: 37px; border: 2px solid var(--deep-blue); display: flex; }
  .badge-wide__red { width: 30px; background: var(--badge-red); }
  .badge-wide__white { flex: 1; background: #fff; }

  .address { position: absolute; left: 52px; top: 292px; color: #fff; }
  .address__street { font-size: 21px; line-height: 1.25; }
  .address__city { font-size: 25px; line-height: 1.2; }

  .contact { position: absolute; right: 58px; top: 286px; color: #fff; text-align: right; }
  .contact__phone { font-size: 36px; line-height: 1.1; letter-spacing: -0.5px; }
  .contact__web { font-size: 18px; line-height: 1.3; }

  .trades { position: absolute; top: 58px; left: 50px; right: 40px; display: flex; gap: 70px; list-style: none; }
  .trades__col { list-style: none; font-family: "Roboto Condensed", sans-serif; font-weight: 300; color: #fff; font-size: 19.5px; line-height: 22px; }
  .trades__col li { display: flex; align-items: center; gap: 10px; }
  .trades__col li::before { content: ""; width: 10px; height: 10px; border-radius: 50%; background: #fff; flex: none; }
  .trades__col--right { margin-left: 0; }

  .fill-fields { position: absolute; left: 52px; right: 54px; top: 272px; font-family: "Roboto Condensed", sans-serif; font-weight: 400; color: var(--line-blue); font-size: 15.5px; }
  .fill-fields__row { display: flex; align-items: flex-end; gap: 4px; height: 20px; }
  .fill-fields__row + .fill-fields__row { margin-top: 34px; }
  .fill-fields__line { flex: 1; border-bottom: 1px solid var(--line-blue); margin-bottom: 4px; }
</style>
</head>
<body>

  <section class="card card--front" aria-label="Business card front">
    <svg class="card__art" viewBox="0 0 800 457" preserveAspectRatio="none" aria-hidden="true">
      <defs>
        <linearGradient id="frontBlue" x1="0" y1="0" x2="1" y2="0">
          <stop offset="0" stop-color="#176aac"/>
          <stop offset="0.55" stop-color="#2f98d0"/>
          <stop offset="1" stop-color="#1e76b8"/>
        </linearGradient>
      </defs>
      <path d="M0,262 Q430,318 800,172 L800,457 L0,457 Z" fill="#4fb3e3"/>
      <path d="M0,272 Q430,330 800,192 L800,457 L0,457 Z" fill="#3a3d42"/>
      <path d="M0,282 Q440,330 800,196 L800,457 L0,457 Z" fill="url(#frontBlue)"/>
    </svg>

    <div class="brand">
      <span class="brand__dot"></span>
      <div>
        <div class="brand__name">HARBORLINE</div>
        <div class="brand__sub">ROOFING &amp; GUTTERS INC.</div>
      </div>
    </div>

    <div class="badges" role="img" aria-label="Accreditation badges">
      <div class="badges__row">
        <span class="badge-tall"></span>
        <span class="badge-hex"></span>
        <span class="badge-round"></span>
      </div>
      <div class="badge-wide"><span class="badge-wide__red"></span><span class="badge-wide__white"></span></div>
    </div>

    <div class="address">
      <p class="address__street">5217 Mallow Creek Ln</p>
      <p class="address__city">Orlando, Fl 32825</p>
    </div>

    <div class="contact">
      <p class="contact__phone">(407)-583-2196</p>
      <p class="contact__web">www.HarborlineRoofsFl.com</p>
    </div>
  </section>

  <section class="card card--back" aria-label="Business card back">
    <svg class="card__art" viewBox="0 0 800 457" preserveAspectRatio="none" aria-hidden="true">
      <defs>
        <linearGradient id="backBlue" x1="0" y1="0" x2="1" y2="0">
          <stop offset="0" stop-color="#176aac"/>
          <stop offset="0.55" stop-color="#2f98d0"/>
          <stop offset="1" stop-color="#1e76b8"/>
        </linearGradient>
      </defs>
      <path d="M0,0 H800 V150 Q430,275 0,236 Z" fill="#3a3d42"/>
      <path d="M0,0 H800 V132 Q430,262 0,226 Z" fill="#4fb3e3"/>
      <path d="M0,0 H800 V146 Q430,258 0,218 Z" fill="url(#backBlue)"/>
    </svg>

    <div class="trades">
      <ul class="trades__col">
        <li>Residential &amp; Commercial</li>
        <li>Fully Insured</li>
        <li>License # CCC7482913</li>
      </ul>
      <ul class="trades__col trades__col--right">
        <li>Insurance Claims</li>
        <li>Serving Central Florida Since 1992</li>
        <li>Free Estimates</li>
      </ul>
    </div>

    <div class="fill-fields">
      <div class="fill-fields__row"><span>PROJECT MANAGER NAME :</span><span class="fill-fields__line"></span></div>
      <div class="fill-fields__row"><span>PHONE:</span><span class="fill-fields__line"></span></div>
    </div>
  </section>

</body>
</html>
```